Building company buisness cards

We are looking for a sharp modern new look for our business cards.
We are a New Zealand based company that specialises in house and land packages.
We have attached a photo of the current logo and would like to see if it can be improved somehow if needed.
We are open to any colours but we have chosen green at this stage.
Feel free to change the font and make the logo smarter looking.
Play with the colours and see what looks best.

We want a card that looks so good know one will want to throw it away!

Target Market(s)

Home buyers

Industry/Entity Type

Building

Contact Information for Business Card

Derek Tolvane
0217394062
dtolvane@quillmarkhomesteads.co.nz
quillmarkhomesteads.co.nz

Font styles to use
Serif
Sans Serif

Colors

Designer to choose colors to be used in the design.

Requirements
Must have
• Logo and company name on one side, details on the other side
Nice to have
• Color codes for the original green are HEX #4a8028, RGB(74,128,40), CMYK(42,0,69,50)
• Round corners, Raised and/or spot UV

```html
<!DOCTYPE html>
<html lang="en">
<head>
<meta charset="utf-8">
<title>Quillmark Homesteads — Business Card</title>
<link rel="stylesheet" href="https://fonts.googleapis.com/css2?family=Nunito:wght@900&family=Lato:wght@400&family=Open+Sans:wght@400&display=swap">
<style>
  :root {
    --brand-green: #4a8028;
    --pale-green: #edf2e8;
    --rule-green: #c9dcbc;
    --ink: #444444;
    --card: #ffffff;
    --backdrop: #e6e6e4;
  }
  * { margin: 0; padding: 0; box-sizing: border-box; }
  html, body { width: 1200px; height: 1200px; overflow: hidden; }
  body { background: var(--backdrop); position: relative; }

  .card {
    position: absolute;
    top: 310px;
    width: 364px;
    height: 594px;
    background: var(--card);
    box-shadow: 0 2px 6px rgba(0,0,0,0.18);
    overflow: hidden;
  }
  .card--details { left: 234px; }
  .card--brand { left: 627px; width: 369px; }

  .wordmark {
    position: absolute;
    left: 0; right: 0;
    text-align: center;
    font-family: 'Nunito', sans-serif;
    font-weight: 900;
    color: var(--brand-green);
    letter-spacing: -0.5px;
    line-height: 1.05;
  }
  .wordmark__rule {
    display: block;
    width: 62px;
    height: 1px;
    margin: 8px auto 0;
    background: var(--rule-green);
  }
  .brand-square {
    position: absolute;
    left: 164px; top: 150px;
    width: 36px; height: 36px;
    background: var(--brand-green);
    border-radius: 4px;
  }
  .card--details .wordmark { top: 204px; font-size: 34px; }

  .person-name {
    position: absolute;
    top: 396px; left: 0; right: 0;
    text-align: center;
    font-family: 'Lato', sans-serif;
    font-size: 21px;
    color: var(--brand-green);
    letter-spacing: 0.2px;
  }
  .contact-icons {
    position: absolute;
    top: 450px; left: 0; right: 0;
    display: flex;
    justify-content: center;
    align-items: center;
    gap: 5px;
  }
  .contact-icons__line { width: 40px; height: 1px; background: #888; margin: 0 3px; }
  .contact-icons svg { display: block; }
  .contact-list {
    position: absolute;
    top: 484px; left: 0; right: 0;
    text-align: center;
    font-family: 'Open Sans', sans-serif;
    font-size: 16px;
    line-height: 21px;
    color: var(--ink);
    list-style: none;
  }

  .backdrop-figure {
    position: absolute;
    left: 0; top: 0; right: 0; bottom: 0;
    background: linear-gradient(180deg, var(--pale-green) 0%, #f4f7f1 100%);
  }
  .card--brand .wordmark { top: 470px; font-size: 36px; }
</style>
</head>
<body>

  <section class="card card--details">
    <span class="brand-square" aria-hidden="true"></span>
    <h1 class="wordmark">quillmark<br>homesteads.<span class="wordmark__rule"></span></h1>

    <p class="person-name">DEREK TOLVANE</p>

    <div class="contact-icons" aria-hidden="true">
      <span class="contact-icons__line"></span>
      <svg width="22" height="22" viewBox="0 0 22 22">
        <rect width="22" height="22" rx="4" fill="#4a8028"/>
        <path d="M7 5 L9.5 5 L10.5 8 L9 9.2 Q10.5 12.2 12.8 13 L14 11.5 L17 12.5 L17 15 Q16 17 13.5 16.4 Q7.5 14.5 5.6 8.5 Q5.2 6 7 5 Z" fill="#fff"/>
      </svg>
      <svg width="22" height="22" viewBox="0 0 22 22">
        <rect width="22" height="22" rx="4" fill="#4a8028"/>
        <rect x="5" y="7" width="12" height="8.5" fill="none" stroke="#fff" stroke-width="1.4"/>
        <path d="M5 7 L11 12 L17 7" fill="none" stroke="#fff" stroke-width="1.4"/>
      </svg>
      <svg width="22" height="22" viewBox="0 0 22 22">
        <rect width="22" height="22" rx="4" fill="#4a8028"/>
        <circle cx="11" cy="11" r="6" fill="none" stroke="#fff" stroke-width="1.4"/>
        <path d="M5 11 H17 M11 5 Q7.5 11 11 17 M11 5 Q14.5 11 11 17" fill="none" stroke="#fff" stroke-width="1"/>
      </svg>
      <span class="contact-icons__line"></span>
    </div>

    <ul class="contact-list">
      <li>0217394062</li>
      <li>dtolvane@quillmarkhomesteads.co.nz</li>
      <li>www.quillmarkhomesteads.co.nz</li>
    </ul>
  </section>

  <section class="card card--brand">
    <div class="backdrop-figure" role="img" aria-label="Large faint pale-green brand figure decoration filling the card"></div>
    <h2 class="wordmark">quillmark<br>homesteads.<span class="wordmark__rule"></span></h2>
  </section>

</body>
</html>
```